Brivolt Technologies business card design

We need a business card designed with our new logo. it would be great if the card could communicate it is a technology based company.

Target Market(s)

system integrators

Industry/Entity Type

technology, IOT

Contact Information for Business Card

Name, designation, Address, telephone number, email address

Requirements
Must have
• logo and company name
Nice to have
• something to do with technology

```html
<!DOCTYPE html>
<html lang="en">
<head>
<meta charset="UTF-8">
<title>Brivolt Technologies – Business Card</title>
<link href="https://fonts.googleapis.com/css2?family=Open+Sans:wght@400;600;700;800&display=swap" rel="stylesheet">
<style>
  :root{
    --backdrop:#3b3b3b;
    --card:#1b1b1b;
    --accent:#f39200;
    --text:#f2f2f2;
    --muted:#d8d8d8;
    --emboss:#3a3a3a;
  }
  *{margin:0;padding:0;box-sizing:border-box}
  html,body{width:1200px;height:801px;overflow:hidden}
  body{
    background:var(--backdrop);
    font-family:"Open Sans",Arial,sans-serif;
    position:relative;
  }
  .card{
    position:absolute;
    width:540px;height:309px;
    background:var(--card);
    border-bottom:2px solid var(--accent);
    border-left:2px solid var(--accent);
    box-shadow:0 14px 30px rgba(0,0,0,.35);
  }
  .card--front{left:36px;top:246px}
  .card--back{left:624px;top:246px}

  /* front */
  .brand{
    position:absolute;left:44px;top:178px;
    display:flex;align-items:center;gap:12px;
    max-width:230px;
  }
  .brand__square{width:34px;height:34px;background:var(--accent);flex:none}
  .brand__name{
    font-weight:800;font-size:20px;line-height:1.1;letter-spacing:.5px;
    color:var(--text);text-transform:uppercase;
  }
  .divider{
    position:absolute;left:302px;top:58px;
    width:2px;height:196px;background:var(--accent);
  }
  .contact{
    position:absolute;left:322px;top:56px;
    color:var(--muted);font-size:12.5px;line-height:1.45;
  }
  .contact__name{
    color:var(--accent);font-weight:700;font-size:17px;
    text-transform:uppercase;line-height:1.2;
  }
  .contact__role{margin-bottom:12px}
  .contact__address{margin-bottom:12px}
  .contact__line{display:flex;align-items:center;gap:8px}
  .contact__line svg{width:11px;height:11px;flex:none}

  /* back */
  .back-brand{
    position:absolute;inset:0;
    display:flex;align-items:center;justify-content:center;gap:16px;
  }
  .back-brand__square{width:44px;height:44px;background:var(--emboss)}
  .back-brand__name{
    font-weight:800;font-size:30px;letter-spacing:1px;
    color:var(--emboss);text-transform:uppercase;
  }
</style>
</head>
<body>
  <section class="card card--front" aria-label="Business card front">
    <div class="brand">
      <span class="brand__square"></span>
      <span class="brand__name">Brivolt<br>Technologies</span>
    </div>
    <div class="divider"></div>
    <div class="contact">
      <p class="contact__name">Daniel Reyes</p>
      <p class="contact__role">President</p>
      <p class="contact__address">1840 Harbor Crest Dr<br>Seaview CA 92610</p>
      <p class="contact__line">
        <svg viewBox="0 0 12 12"><circle cx="6" cy="6" r="6" fill="var(--accent)"/><path d="M4 3.2l1 1.6-.6.6a4 4 0 0 0 2.2 2.2l.6-.6 1.6 1-.6 1C5.8 9 3 6.2 3 3.8z" fill="var(--card)"/></svg>
        949-555-0187
      </p>
      <p class="contact__line">
        <svg viewBox="0 0 12 12"><rect x="1" y="2.5" width="10" height="7" fill="var(--accent)"/><path d="M1 2.5l5 4 5-4" fill="none" stroke="var(--card)" stroke-width="1"/></svg>
        info@brivolttech.com
      </p>
      <p class="contact__line">
        <svg viewBox="0 0 12 12"><circle cx="6" cy="6" r="5.5" fill="var(--accent)"/><path d="M1 6h10M6 .5c-2.2 2.8-2.2 8.2 0 11M6 .5c2.2 2.8 2.2 8.2 0 11" fill="none" stroke="var(--card)" stroke-width=".8"/></svg>
        www.brivolttech.com
      </p>
    </div>
  </section>

  <section class="card card--back" aria-label="Business card back">
    <div class="back-brand">
      <span class="back-brand__square"></span>
      <span class="back-brand__name">Brivolt Technologies</span>
    </div>
  </section>
</body>
</html>
```